Velorin Wine Label For Canopy Haven

Lantern Brook Winery is in need of a wine label for new wine being release. This wine will be used as a fundraiser for Canopy Haven, a chimpanzee santuary in Georgia. The label should reflect a high-end, classy image and the label should suggest the chimp philanthropy without specifically naming the organization (for legal purposes). The label can be a little whimsical without being too cartoonish or child like. This wine will be sold for $30 so it should project a sense of elegance too.
Updates

holiday season makes it difficult to get feedback necessary for approval. just need a few more days...

Industry/Entity Type

Winery

Font styles to use
Sans Serif

Requirements
Must have
• Label should show common design appearance as other labels downloaded.
• Label should be a dark (emerald) green color. Label should have wine name "Velorin" in center. Label should include an image or silhouette of a chimp on it
Should not have
• no cartoonish images;

```html
<!DOCTYPE html>
<html lang="en">
<head>
<meta charset="utf-8">
<title>Velorin Red Wine Label</title>
<link rel="stylesheet" href="https://fonts.googleapis.com/css2?family=Cinzel:wght@700&family=Oswald:wght@400;500&family=Libre+Baskerville&display=swap">
<style>
  :root {
    --paper: #ffffff;
    --emerald: #0b6a34;
    --emerald-deep: #08552a;
    --emerald-edge: #0f5a30;
    --gold: #b58f1a;
    --gold-light: #c29a22;
  }
  html, body {
    margin: 0;
    padding: 0;
    width: 1200px;
    height: 999px;
    overflow: hidden;
    background: var(--paper);
  }
  .label {
    position: relative;
    width: 1200px;
    height: 999px;
    color: var(--gold);
  }
  .label-shapes {
    position: absolute;
    inset: 0;
  }
  .art-slot {
    position: absolute;
    background: var(--gold);
    opacity: 0.85;
  }
  .art-tree-chimp {
    left: 72px; top: 255px; width: 160px; height: 120px;
    border-radius: 50% 50% 12px 12px;
  }
  .art-chimp-walking {
    left: 535px; top: 640px; width: 140px; height: 112px;
    border-radius: 45% 45% 8px 8px;
  }
  .cause-story {
    position: absolute;
    left: 60px; top: 414px; width: 212px;
    font-family: "Libre Baskerville", serif;
    font-size: 10.6px;
    line-height: 13.4px;
    text-align: justify;
  }
  .cause-story p { margin: 0 0 14px; }
  .brand-mark {
    position: absolute;
    left: 500px; top: 172px; width: 200px;
    text-align: center;
  }
  .brand-square {
    display: block;
    width: 40px; height: 40px;
    margin: 12px auto 30px;
    background: var(--gold);
    opacity: 0.8;
    transform: rotate(45deg);
  }
  .brand-name {
    font-family: "Oswald", sans-serif;
    font-weight: 400;
    font-size: 30px;
    line-height: 30px;
    letter-spacing: 2px;
    margin: 0;
  }
  .brand-sub {
    font-family: "Oswald", sans-serif;
    font-weight: 400;
    font-size: 21px;
    letter-spacing: 3px;
    margin: 0;
  }
  .wine-name {
    position: absolute;
    left: 380px; top: 420px; width: 440px;
    margin: 0;
    text-align: center;
    font-family: "Cinzel", serif;
    font-weight: 700;
    font-size: 84px;
    line-height: 96px;
    letter-spacing: 1px;
  }
  .wine-type {
    position: absolute;
    left: 400px; top: 514px; width: 400px;
    margin: 0;
    text-align: center;
    font-family: "Cinzel", serif;
    font-weight: 700;
    font-size: 28px;
    letter-spacing: 1px;
  }
  .spec {
    position: absolute;
    top: 750px;
    font-family: "Oswald", sans-serif;
    font-size: 17px;
    letter-spacing: 0.5px;
  }
  .spec-abv { left: 320px; }
  .spec-volume { left: 766px; }
  .gov-warning {
    position: absolute;
    left: 928px; top: 233px; width: 212px;
    font-family: "Oswald", sans-serif;
    text-transform: uppercase;
  }
  .gov-warning h2 {
    margin: 0 0 2px;
    font-size: 17px;
    font-weight: 500;
    line-height: 22px;
  }
  .gov-warning p {
    margin: 0;
    font-size: 13.6px;
    line-height: 22.5px;
    text-align: justify;
    letter-spacing: 0.3px;
  }
  .producer {
    position: absolute;
    left: 900px; width: 266px;
    margin: 0;
    text-align: center;
    font-family: "Oswald", sans-serif;
    text-transform: uppercase;
  }
  .producer-address { top: 612px; font-size: 18px; line-height: 23px; }
  .producer-web { top: 706px; font-size: 14px; text-transform: none; }
  .producer-sulfites { top: 757px; font-size: 15px; }
</style>
</head>
<body>
<div class="label">
  <svg class="label-shapes" width="1200" height="999" viewBox="0 0 1200 999" aria-hidden="true">
    <defs>
      <radialGradient id="emeraldGlow" cx="50%" cy="50%" r="60%">
        <stop offset="0%" stop-color="var(--emerald)"/>
        <stop offset="100%" stop-color="var(--emerald-deep)"/>
      </radialGradient>
    </defs>
    <!-- horizontal band -->
    <rect x="16" y="188" width="1168" height="622" fill="url(#emeraldGlow)"/>
    <rect x="40" y="206" width="1120" height="588" fill="none" stroke="var(--gold)" stroke-width="6"/>
    <!-- central diamond -->
    <polygon points="600,80 900,498 600,916 300,498" fill="var(--emerald)"/>
    <polygon points="600,96 888,498 600,900 312,498" fill="none" stroke="var(--gold)" stroke-width="3"/>
    <polygon points="600,114 874,498 600,882 326,498" fill="none" stroke="var(--gold)" stroke-width="6"/>
    <!-- title rules -->
    <path d="M396,412 Q600,372 804,412 L804,406 Q600,366 396,406 Z" fill="var(--gold)"/>
    <rect x="388" y="572" width="424" height="4" fill="var(--gold)"/>
    <rect x="384" y="581" width="432" height="7" fill="var(--gold)"/>
    <!-- quality seal -->
    <circle cx="1033" cy="532" r="58" fill="var(--gold)"/>
    <circle cx="1033" cy="532" r="44" fill="none" stroke="var(--emerald-edge)" stroke-width="2"/>
  </svg>

  <div class="art-slot art-tree-chimp" role="img" aria-label="Gold silhouette of a tree with a chimpanzee walking beside it"></div>

  <div class="cause-story">
    <p>A Public awareness campaign design and dedicated to provide lifetime exemplary care to more than 200 chimpanzees.</p>
    <p>September 14, 2015, marked the effective end of unrestricted invasive experiments on chimpanzees in the United States. All chimps, both wild and captive, were listed as endangered under the Endangered Species Act (ESA) on that day, after a decades-long fight to end the use of chimpanzees in laboratory research.</p>
    <p>We support a forever home sanctuary to all of chimpanzees in that laboratory research.</p>
    <p>A portion of this wine sale will go to support this campaign.</p>
    <p>Join the Movement.</p>
  </div>

  <div class="brand-mark">
    <span class="brand-square"></span>
    <p class="brand-name">LANTERN</p>
    <p class="brand-sub">· BROOK ·</p>
  </div>

  <h1 class="wine-name">VELORIN</h1>
  <p class="wine-type">Red Wine</p>

  <div class="art-slot art-chimp-walking" role="img" aria-label="Gold silhouette of a chimpanzee walking on all fours"></div>

  <span class="spec spec-abv">12.6% ALC./VOL</span>
  <span class="spec spec-volume">750ML</span>

  <div class="gov-warning">
    <h2>Government Warning:</h2>
    <p>(1) According to the Surgeon General, women should not drink alcoholic beverages during pregnancy because of the risk of birth defects.</p>
    <p>(2) Consumption of alcoholic beverages impairs your ability to drive a car or operate machinery, and may cause health problems.</p>
  </div>

  <p class="producer producer-address">Produced &amp; Bottled at<br>Lantern Brook, Resort &amp; Spa<br>Ridgeview GA</p>
  <p class="producer producer-web">www.lanternbrookwine.com</p>
  <p class="producer producer-sulfites">Contain Sulfites</p>
</div>
</body>
</html>
```